Commercial Real Estate

We need a business card design for a new commercial real estate business that specializes in apartment building brokerage. Not individual units but the entire complex. We find and represent the owners existing buildings and well as new buyers for those buildings. The design should convey trust, integrity, knowledge and growth. It should be easily read.

Target Market(s)

40 to 65 years old

Industry/Entity Type

Real Estate

```html
<!DOCTYPE html>
<html lang="en">
<head>
<meta charset="utf-8">
<title>Halvora Property Investments – Business Card</title>
<link href="https://fonts.googleapis.com/css2?family=Lato:wght@400;700;900&display=swap" rel="stylesheet">
<style>
  :root {
    --backdrop: #2b2b2b;
    --card: #ffffff;
    --teal: #5cbcbc;
    --ink: #3f4a4a;
    --ink-soft: #555e5e;
  }
  * { margin: 0; padding: 0; box-sizing: border-box; }
  html, body {
    width: 1200px; height: 900px; overflow: hidden;
    background: var(--backdrop);
    font-family: "Lato", sans-serif;
  }
  .stage {
    width: 1200px; height: 900px;
    display: flex; align-items: center; justify-content: center;
  }
  .card {
    position: relative;
    width: 1000px; height: 572px;
    background: var(--card);
    box-shadow: 0 12px 40px rgba(0,0,0,.45);
  }
  .brand {
    position: absolute;
    left: 70px; top: 0; bottom: 0; width: 420px;
    display: flex; flex-direction: column; justify-content: center; align-items: flex-start;
    gap: 18px;
  }
  .brand-mark {
    width: 44px; height: 44px; background: var(--teal);
  }
  .brand-name {
    font-weight: 900; font-size: 64px; letter-spacing: 3px;
    color: var(--ink); line-height: 1;
  }
  .brand-tagline {
    font-weight: 900; font-size: 22px; letter-spacing: 6px;
    color: var(--ink); line-height: 1;
    border-top: 3px solid var(--teal); padding-top: 10px;
  }
  .divider {
    position: absolute;
    left: 560px; top: 150px; width: 6px; height: 320px;
    background: linear-gradient(to bottom, rgba(92,188,188,0), var(--teal) 40%, var(--teal));
  }
  .person {
    position: absolute; left: 560px; top: 86px;
  }
  .person-name {
    font-weight: 900; font-size: 30px; color: var(--teal); letter-spacing: .5px;
  }
  .person-role {
    font-weight: 700; font-size: 17px; color: var(--ink); letter-spacing: .5px; margin-top: 2px;
  }
  .contact {
    position: absolute; left: 600px; top: 196px;
    list-style: none;
  }
  .address {
    font-weight: 900; font-size: 22px; color: var(--teal); line-height: 1.25;
    margin-bottom: 14px;
  }
  .contact-line {
    display: flex; align-items: center; gap: 18px;
    font-size: 23px; font-weight: 400; color: var(--ink); letter-spacing: .5px;
    height: 44px;
  }
  .contact-line svg { width: 26px; height: 26px; flex: none; }
  .icon-fill { fill: var(--teal); }
  .icon-stroke { fill: none; stroke: var(--teal); stroke-width: 2; }
  .web {
    margin-top: 16px; font-weight: 900; font-size: 25px; color: var(--ink);
  }
  .web span { color: var(--teal); }
</style>
</head>
<body>
<main class="stage">
  <section class="card">
    <div class="brand">
      <div class="brand-mark"></div>
      <div class="brand-name">HALVORA</div>
      <div class="brand-tagline">Property Investments</div>
    </div>

    <div class="divider"></div>

    <header class="person">
      <div class="person-name">YOUR NAME</div>
      <div class="person-role">DESIGNATION</div>
    </header>

    <ul class="contact">
      <li class="address">8 Place Verlaine,<br>94200 Ivry sur Seine</li>
      <li class="contact-line">
        <svg viewBox="0 0 26 26" aria-hidden="true"><path class="icon-fill" d="M3 10c0-3 4-5 10-5s10 2 10 5v2h-5v-2H8v2H3z"/><path class="icon-fill" d="M7 13h12l3 8H4z"/></svg>
        555.014.2283
      </li>
      <li class="contact-line">
        <svg viewBox="0 0 26 26" aria-hidden="true"><rect class="icon-stroke" x="7" y="2" width="12" height="22" rx="2"/><line class="icon-stroke" x1="11" y1="20" x2="15" y2="20"/></svg>
        +33 (0)6 00 12 34 56
      </li>
      <li class="contact-line">
        <svg viewBox="0 0 26 26" aria-hidden="true"><rect class="icon-fill" x="7" y="3" width="12" height="6"/><rect class="icon-fill" x="2" y="10" width="22" height="9" rx="2"/><rect class="icon-fill" x="7" y="20" width="12" height="4"/></svg>
        +33 (0)1 00 98 76 54
      </li>
      <li class="contact-line">
        <svg viewBox="0 0 26 26" aria-hidden="true"><rect class="icon-fill" x="2" y="5" width="22" height="16"/><path d="M2 5l11 9 11-9" fill="none" stroke="#fff" stroke-width="2"/></svg>
        Info@halvorainvestments.com
      </li>
      <li class="web">www.<span>halvorainvestments</span>.com</li>
    </ul>
  </section>
</main>
</body>
</html>
```